Velmora Freightway Solutions Business cards

Would like a very unique design catchy but professional for business cards. Please use log provided.Marlon WellsCeo and Founder TransCon Logistix Solutions1-888-913-3225mwells@tlsolutionsus.comwww.tlsolutionsus.com

```html
<!DOCTYPE html>
<html lang="en">
<head>
<meta charset="utf-8">
<title>Velmora Freightway Solutions – Business Cards</title>
<link href="https://fonts.googleapis.com/css2?family=Montserrat:wght@600&family=Open+Sans:wght@400;600&display=swap" rel="stylesheet">
<style>
  :root {
    --blue: #1a8ccc;
    --blue-deep: #0f6fab;
    --red: #e8343f;
    --white: #f7f7f7;
    --ink-light: #e6f3fb;
    --page: #e9e6e1;
  }
  * { box-sizing: border-box; margin: 0; padding: 0; }
  html, body { width: 1200px; height: 780px; overflow: hidden; }
  body {
    background: var(--page);
    display: flex;
    align-items: center;
    justify-content: center;
    gap: 50px;
    font-family: "Open Sans", Arial, sans-serif;
  }
  .card {
    width: 540px;
    height: 310px;
    border-radius: 18px;
    overflow: hidden;
    box-shadow: 0 6px 18px rgba(0,0,0,0.18);
    position: relative;
  }
  /* Front */
  .card-front { display: flex; flex-direction: column; background: var(--white); }
  .front-brand {
    flex: 0 0 168px;
    display: flex;
    align-items: center;
    justify-content: center;
  }
  .brand-name {
    font-family: "Montserrat", Arial, sans-serif;
    font-weight: 600;
    font-size: 25px;
    letter-spacing: 1px;
    text-transform: uppercase;
    text-align: center;
    line-height: 1.25;
  }
  .front-brand .brand-name { color: var(--blue); }
  .name-band {
    flex: 0 0 48px;
    background: var(--red);
    border-bottom: 3px solid #fff;
    color: #fff;
    display: flex;
    flex-direction: column;
    justify-content: center;
    padding-left: 210px;
    line-height: 1.1;
  }
  .person-name { font-weight: 600; font-size: 19px; }
  .person-title { font-size: 12px; }
  .contact-band {
    flex: 1;
    background: linear-gradient(180deg, var(--blue) 0%, var(--blue-deep) 100%);
    color: var(--ink-light);
    font-size: 13px;
    padding: 26px 0 0 90px;
    line-height: 1.9;
  }
  /* Back */
  .card-back {
    background: radial-gradient(ellipse at 50% 45%, #2aa0dd 0%, var(--blue) 45%, var(--blue-deep) 100%);
    display: flex;
    align-items: center;
    justify-content: center;
  }
  .card-back .brand-name { color: #fff; }
</style>
</head>
<body>
  <div class="card card-front">
    <div class="front-brand">
      <p class="brand-name">Velmora Freightway<br>Solutions</p>
    </div>
    <div class="name-band">
      <span class="person-name">Dorian Pike</span>
      <span class="person-title">Ceo and Founder</span>
    </div>
    <div class="contact-band">
      <p>P: 1-888-470-6158 | E: dpike@vfwayroutes.com</p>
      <p>www.vfwayroutes.com</p>
    </div>
  </div>

  <div class="card card-back">
    <p class="brand-name">Velmora Freightway<br>Solutions</p>
  </div>
</body>
</html>
```